Kestal-Materials. Limestone; improving the world

New Limestone company and need logo design.
Limestone offsets carbon mitigation industries restore and replenish soil fertilities in the Prairies, the breadbasket of the world. At the same time, Limestone is proving a critical emergent component of carbon capture sequestration technology will therefore play a critical role in the development of the western Canadian energy industries
Our limestone resources are situated in the foothills of the Canadian Rockies well-positioned above the sprawling fields of the vast peace district.
Agriculture and oli sites
Kestal Materials
3 page

```html
<!DOCTYPE html>
<html lang="en">
<head>
<meta charset="UTF-8">
<title>Kestal Materials</title>
<link href="https://fonts.googleapis.com/css2?family=Ubuntu:wght@400;500;700&display=swap" rel="stylesheet">
<style>
  :root {
    --blue: #2a7fd4;
    --green: #5ea122;
    --ink: #1f1f1f;
    --text: #2b2b2b;
    --footer: #1e1e1e;
    --white: #ffffff;
    --circle: rgba(105, 105, 105, 0.86);
  }
  * { margin: 0; padding: 0; box-sizing: border-box; }
  html, body { width: 1200px; height: 3945px; overflow: hidden; }
  body { position: relative; background: var(--white); font-family: "Ubuntu", sans-serif; color: var(--text); }
  .abs { position: absolute; }

  /* Hero */
  .hero { left: 0; top: 0; width: 1200px; height: 870px;
    background: linear-gradient(180deg, #e9f4f8 0%, #9fd2e0 22%, #7fbccd 38%, #b57a55 55%, #8a4a2d 72%, #6e3a24 100%); }
  .hero-wave { left: 0; top: 560px; width: 1200px; height: 320px; }
  .header { left: 0; top: 0; width: 1200px; height: 100px; }
  .brand { left: 173px; top: 34px; display: flex; align-items: center; gap: 12px;
    font-weight: 700; font-size: 24px; color: var(--blue); text-transform: uppercase; letter-spacing: 1px; }
  .brand-dot { width: 36px; height: 36px; border-radius: 50%; background: var(--blue); }
  .nav { left: 534px; top: 47px; width: 495px; display: flex; justify-content: space-between;
    font-size: 12.5px; color: var(--ink); text-transform: uppercase; list-style: none; }
  .hero-title { left: 0; top: 180px; width: 1200px; text-align: center; color: var(--white);
    font-weight: 700; font-size: 58px; line-height: 76px; letter-spacing: 4px; text-transform: uppercase;
    text-shadow: 0 2px 4px rgba(0,0,0,0.25); }
  .dots { left: 0; top: 364px; width: 1200px; display: flex; justify-content: center; gap: 10px; }
  .dots span { width: 17px; height: 17px; border-radius: 50%; background: rgba(255,255,255,0.5); }
  .dots span:first-child { background: var(--white); }

  h2 { font-weight: 500; color: var(--blue); font-size: 30px; text-transform: uppercase; }
  .centered { text-align: center; }
  .body-text { font-size: 13.5px; line-height: 24px; color: var(--text); }

  .intro-title { left: 0; top: 944px; width: 1200px; }
  .intro-text { left: 176px; top: 1006px; width: 848px; text-align: center; }

  .frame { border: 3px solid var(--blue); border-radius: 22px; }
  .photo { border-radius: 22px; }
  .who-frame { left: 158px; top: 1173px; width: 330px; height: 280px; }
  .who-photo { left: 173px; top: 1187px; width: 329px; height: 283px;
    background: linear-gradient(180deg, #c9c2a8 0%, #d9b883 30%, #8b8f7a 55%, #6d7072 100%); }
  .who-title { left: 547px; top: 1185px; }
  .who-text { left: 547px; top: 1234px; width: 482px; }
  .btn { display: flex; align-items: center; justify-content: center; background: var(--green);
    color: var(--white); font-weight: 500; font-size: 14px; border-radius: 8px; text-transform: uppercase; }
  .who-btn { left: 547px; top: 1398px; width: 114px; height: 55px; }

  .products-title { left: 0; top: 1588px; width: 1200px; }
  .products-band { left: 0; top: 1760px; width: 1200px; height: 494px;
    background: linear-gradient(180deg, #b9c79a 0%, #8aa356 20%, #4f7a3a 50%, #2f5a32 80%, #284c2c 100%); }
  .product { width: 257px; height: 257px; border-radius: 50%; background: var(--circle);
    color: var(--white); text-align: center; padding-top: 36px; }
  .product-num { font-size: 44px; font-weight: 500; line-height: 50px; }
  .product-name { font-size: 20px; margin-top: 10px; text-transform: uppercase; }
  .product-text { font-size: 13px; line-height: 24px; width: 190px; margin: 6px auto 0; }

  .markets-title { left: 0; top: 2330px; width: 1200px; }
  .market { width: 274px; height: 398px; background: var(--white); border-radius: 14px;
    box-shadow: 0 2px 14px rgba(0,0,0,0.14); padding: 11px; text-align: center; }
  .market-photo { width: 252px; height: 191px; border-radius: 12px; }
  .market-name { font-size: 21px; color: var(--ink); margin-top: 30px; text-transform: uppercase; }
  .market-text { font-size: 13px; line-height: 24px; margin-top: 10px; padding: 0 8px; }

  .sus-title { left: 173px; top: 2984px; }
  .sus-text { left: 173px; top: 3035px; width: 458px; }
  .sus-btn { left: 173px; top: 3198px; width: 115px; height: 55px; }
  .sus-frame { left: 666px; top: 2929px; width: 425px; height: 355px; }
  .sus-photo { left: 684px; top: 2949px; width: 423px; height: 363px;
    background: linear-gradient(135deg, #bfbfbd 0%, #9b9b98 40%, #b8a894 60%, #8c8d8b 100%); }

  .footer { left: 0; top: 3430px; width: 1200px; height: 515px; background: var(--footer); color: var(--white); }
  .footer-col { top: 91px; list-style: none; font-size: 12.5px; }
  .footer-col .head { font-size: 15px; text-transform: uppercase; margin-bottom: 12px; }
  .footer-col li { line-height: 27px; }
  .footer-rule { left: 173px; top: 421px; width: 856px; height: 1px; background: #cfcfcf; }
  .copyright { left: 0; top: 458px; width: 1200px; text-align: center; font-size: 12.5px; }
</style>
</head>
<body>

<section class="abs hero" role="img" aria-label="Red rock spires under a blue sky"></section>
<svg class="abs hero-wave" viewBox="0 0 1200 320" preserveAspectRatio="none">
  <path fill="#ffffff" d="M0 220 C90 160 170 90 230 150 C260 180 240 280 320 285 C500 290 620 180 720 180 C800 180 820 270 870 300 C930 330 1010 220 1080 160 C1130 120 1170 110 1200 120 L1200 320 L0 320 Z"/>
</svg>

<header class="abs header">
  <div class="abs brand"><span class="brand-dot"></span>Kestal Materials</div>
  <ul class="abs nav">
    <li>Products</li><li>Markets</li><li>Locations</li><li>Sustainability</li><li>About Us</li><li>Careers</li>
  </ul>
</header>

<h1 class="abs hero-title">Kestal<br>Materials</h1>
<div class="abs dots"><span></span><span></span><span></span></div>

<h2 class="abs intro-title centered">World-class in everything we do!</h2>
<p class="abs intro-text body-text">Nam libero tempore, cum soluta nobis est eligendi optio cumque nihil impedit quo minus id quod maxime placeat facere possimus, omnis voluptas assumenda est, omnis dolor repellendus. Temporibus autem quibusdam et aut officiis debitis aut rerum necessitatibus saepe eve niet ut et voluptates repudiandae sint et molestiae non recusandae. Itaque earum rerum hic tenetur a sapiente delectus, ut aut reiciendis voluptatibus maiores alias consequatur aut perferendis doloribus asperiores repellat.</p>

<div class="abs frame who-frame"></div>
<div class="abs photo who-photo" role="img" aria-label="Limestone pavement with a lone tree at sunset"></div>
<h2 class="abs who-title">Who we are</h2>
<p class="abs who-text body-text">Nam libero tempore, cum soluta nobis est eligendi optio cumque nihil impedit quo minus id quod maxime placeat facere possimus, omnis voluptas assumenda est, omnis dolor repellendus. Temporibus autem quibusdam et aut officiis debi tis aut rerum necessitatibus saepe eve niet ut et voluptates repudiandae sint et molestiae non recusandae. Itaque earum rerum hic tenetur a sapiente delectus, ut aut reiciendis voluptatibus.</p>
<div class="abs btn who-btn">Read more</div>

<h2 class="abs products-title centered">Our products</h2>
<div class="abs products-band" role="img" aria-label="Green crop field stretching to the horizon"></div>
<div class="abs product" style="left:172px;top:1677px">
  <div class="product-num">01</div><div class="product-name">Quicklime</div>
  <p class="product-text">Temporibus autem quibusdam et aut officiis debi tis aut rerum necessit.</p>
</div>
<div class="abs product" style="left:472px;top:1677px">
  <div class="product-num">02</div><div class="product-name">Hydrated Lime</div>
  <p class="product-text">Temporibus autem quibusdam et aut officiis debi tis aut rerum necessit.</p>
</div>
<div class="abs product" style="left:772px;top:1677px">
  <div class="product-num">03</div><div class="product-name">Pulverized Limestone</div>
  <p class="product-text">Temporibus autem quibusdam et aut officiis debi tis aut rerum necessit.</p>
</div>
<div class="abs product" style="left:322px;top:1916px">
  <div class="product-num">04</div><div class="product-name">Chemical Limestone</div>
  <p class="product-text">Temporibus autem quibusdam et aut officiis debi tis aut rerum necessit.</p>
</div>
<div class="abs product" style="left:622px;top:1916px">
  <div class="product-num">05</div><div class="product-name">Construction Stone</div>
  <p class="product-text">Temporibus autem quibusdam et aut officiis debi tis aut rerum necessit.</p>
</div>

<h2 class="abs markets-title centered">Our markets</h2>
<article class="abs market" style="left:173px;top:2413px">
  <div class="market-photo" role="img" aria-label="Yellow haul trucks in an open-pit mine" style="background:linear-gradient(180deg,#8a8174,#5b554d 60%,#3c3a36)"></div>
  <h3 class="market-name" style="font-weight:400">Mining</h3>
  <p class="market-text">At vero eos et accusamus et iusto odio dignissimos ducimus qui blanditiis praesentium voluptatum deleniti atque corrupti quos.</p>
</article>
<article class="abs market" style="left:462px;top:2413px">
  <div class="market-photo" role="img" aria-label="Stacked steel pipes" style="background:linear-gradient(180deg,#5d6063,#2c2e30 55%,#6b6e70)"></div>
  <h3 class="market-name" style="font-weight:400">Steel</h3>
  <p class="market-text">At vero eos et accusamus et iusto odio dignissimos ducimus qui blanditiis praesentium voluptatum deleniti atque corrupti quos.</p>
</article>
<article class="abs market" style="left:753px;top:2413px">
  <div class="market-photo" role="img" aria-label="Seedlings growing in front of a city skyline" style="background:linear-gradient(180deg,#c9d2d8,#aab4b3 60%,#5a5348)"></div>
  <h3 class="market-name" style="font-weight:400">Environmental</h3>
  <p class="market-text">At vero eos et accusamus et iusto odio dignissimos ducimus qui blanditiis praesentium voluptatum deleniti atque corrupti quos.</p>
</article>

<h2 class="abs sus-title">Sustainability</h2>
<p class="abs sus-text body-text">Nam libero tempore, cum soluta nobis est eligendi optio cumque nihil im pedit quo minus id quod maxime placeat facere possimus, omnis voluptas assumenda est, omnis dolor repellendus. Temporibus autem quibusdam et aut officiis debi tis aut rerum necessitatibus saepe eve niet ut et voluptates repudiandae sint et molestiae non recusandae. Itaque earum rerum hic te netur a sapiente delectus.</p>
<div class="abs btn sus-btn">Read more</div>
<div class="abs frame sus-frame"></div>
<div class="abs photo sus-photo" role="img" aria-label="Hands holding pieces of grey limestone over gravel"></div>

<footer class="abs footer">
  <ul class="abs footer-col" style="left:173px">
    <li class="head">Home</li><li>CUSTOMER PORTAL</li><li>WHAT IS LIME?</li><li>NEWS</li><li>CONTACT US</li>
  </ul>
  <ul class="abs footer-col" style="left:375px">
    <li class="head">Products</li><li>Quicklime</li><li>Hydrated Lime</li><li>Pulverized Limestone</li><li>Chemical Limestone</li><li>Construction Stone</li><li>Co-products</li><li>Safety Data Sheets (SDS)</li><li>Technical Information</li>
  </ul>
  <ul class="abs footer-col" style="left:629px">
    <li class="head">Markets</li><li>Mining</li><li>Steel</li><li>Environmental</li><li>Pulp &amp; Paper</li><li>Glass</li><li>Agriculture</li><li>Food</li><li>Building Construction</li><li>Construction Materials</li>
  </ul>
  <ul class="abs footer-col" style="left:868px">
    <li class="head">About Us</li><li>Who We Are</li><li>Mission, Vision &amp; Values</li><li>Strategic Leadership Team</li><li>Workforce Culture</li><li>Customer Services</li><li>Brochures</li>
  </ul>
  <div class="abs footer-rule"></div>
  <p class="abs copyright">Copyrights @ 2021 Kestal Materials. All Rights Reserved.</p>
</footer>

</body>
</html>
```